Letterhead Design Project

I need letterhead designed for my law firm. It would also be used for web based stuff as well.

Industry/Entity Type

Law Firm

```html
<!DOCTYPE html>
<html lang="en">
<head>
<meta charset="utf-8">
<title>Hartwell &amp; Okafor – Letterhead</title>
<link rel="stylesheet" href="https://fonts.googleapis.com/css2?family=PT+Sans:wght@400&display=swap">
<style>
  :root {
    --stage: #000000;
    --paper: #ffffff;
    --navy: #28287a;
    --ink: #2e3192;
    --label: #ffffff;
    --portrait-left: #4a4a4e;
    --portrait-right: #3a2c24;
  }
  * { margin: 0; padding: 0; box-sizing: border-box; }
  html, body {
    width: 1200px;
    height: 1000px;
    overflow: hidden;
    background: var(--stage);
  }
  .letterhead {
    position: absolute;
    left: 272px;
    top: 36px;
    width: 673px;
    height: 945px;
    background: var(--paper);
    font-family: "PT Sans", sans-serif;
  }
  .brand-block {
    position: absolute;
    left: 7px;
    top: 8px;
    width: 209px;
    height: 209px;
    background: var(--navy);
  }
  .brand-name {
    position: absolute;
    left: 0;
    top: 12px;
    width: 209px;
    color: var(--label);
    font-weight: 400;
    font-size: 19px;
    line-height: 30px;
    text-align: center;
    white-space: nowrap;
  }
  .portrait {
    position: absolute;
  }
  .portrait--partner-one {
    left: 14px;
    top: 96px;
    width: 73px;
    height: 88px;
    background: linear-gradient(180deg, #6a6a70 0%, var(--portrait-left) 100%);
  }
  .portrait--partner-two {
    left: 127px;
    top: 94px;
    width: 76px;
    height: 94px;
    background: linear-gradient(180deg, #5a4636 0%, var(--portrait-right) 100%);
  }
  .contact {
    position: absolute;
    left: 423px;
    top: 19px;
    color: var(--ink);
    font-size: 20px;
    line-height: 27.5px;
    font-style: normal;
    white-space: nowrap;
  }
  .contact p + p { margin-top: 28px; }
  .divider {
    position: absolute;
    left: 0;
    top: 224px;
    width: 673px;
    height: 9px;
  }
</style>
</head>
<body>
  <main class="letterhead">
    <div class="brand-block">
      <div class="brand-name">Hartwell &amp; Okafor<br>Law Firm</div>
      <div class="portrait portrait--partner-one" role="img" aria-label="Portrait photo of the first partner"></div>
      <div class="portrait portrait--partner-two" role="img" aria-label="Portrait photo of the second partner"></div>
    </div>

    <address class="contact">
      <p>P.O.BOX 51-7093<br>Madison,WI 53791</p>
      <p>(555)204-7718<br>Hartwellokafor@mail.com</p>
      <p>www.hartwell&amp;okafor.com</p>
    </address>

    <svg class="divider" viewBox="0 0 673 9" aria-hidden="true">
      <line x1="0" y1="4.5" x2="673" y2="4.5" stroke="var(--navy)" stroke-width="9" stroke-dasharray="10 14"/>
    </svg>
  </main>
</body>
</html>
```